Business card design for my company.
I would like the card's background colour to be black. You can also see our web site to get an idea of our brand. https://www.tmwhomecrafting.com.au/
- Name
- Email

```html
<!DOCTYPE html>
<html lang="en">
<head>
<meta charset="utf-8">
<title>TMW Home Crafting — Business Card</title>
<link rel="stylesheet" href="https://fonts.googleapis.com/css2?family=Montserrat:wght@400;500;700&display=swap">
<style>
  :root {
    --stage: #2b2b2b;
    --card: #141414;
    --card-back: #0e0e0e;
    --green: #1f9a48;
    --white: #f2f2f2;
    --muted: #d9d9d9;
    --gloss: #3a3a3a;
  }
  * { box-sizing: border-box; margin: 0; padding: 0; }
  html, body {
    width: 1200px; height: 900px; overflow: hidden;
    background: var(--stage);
    font-family: "Montserrat", sans-serif;
  }
  .stage {
    width: 1200px; height: 900px;
    display: flex; flex-direction: column;
    align-items: center; justify-content: center; gap: 48px;
  }
  .card {
    width: 616px; height: 352px;
    border-radius: 26px;
    background: var(--card);
    box-shadow: 0 18px 40px rgba(0,0,0,.45);
    position: relative;
  }
  /* Front */
  .card-front { display: flex; align-items: center; padding: 0 44px; }
  .brand {
    width: 230px;
    display: flex; align-items: center; gap: 12px;
  }
  .brand-mark { width: 16px; height: 16px; background: var(--green); flex: none; }
  .brand-name {
    font-weight: 700; font-size: 26px; line-height: 1.15;
    color: var(--white); letter-spacing: .5px;
  }
  .divider {
    width: 1.5px; height: 170px; background: var(--green);
    margin: 0 28px 0 18px;
  }
  .details { display: flex; flex-direction: column; }
  .person-name { font-weight: 700; font-size: 27px; color: var(--green); }
  .person-role { font-size: 15px; color: var(--muted); margin-top: 4px; }
  .location { font-size: 15px; color: var(--muted); margin-top: 18px; }
  .contacts { list-style: none; margin-top: 14px; }
  .contacts li {
    display: flex; align-items: center; gap: 9px;
    font-size: 15px; color: var(--muted); line-height: 1.6;
  }
  .contacts svg { width: 12px; height: 12px; fill: var(--green); flex: none; }
  /* Back */
  .card-back {
    background: var(--card-back);
    display: flex; align-items: center; justify-content: center; gap: 18px;
  }
  .back-mark { width: 30px; height: 30px; background: var(--gloss); }
  .back-name {
    font-weight: 700; font-size: 50px; color: var(--gloss); letter-spacing: 1px;
  }
</style>
</head>
<body>
<main class="stage">
  <section class="card card-front" aria-label="Business card front">
    <div class="brand">
      <span class="brand-mark"></span>
      <span class="brand-name">TMW Home Crafting</span>
    </div>
    <div class="divider"></div>
    <div class="details">
      <h1 class="person-name">Liam Hartley</h1>
      <p class="person-role">General Manager</p>
      <p class="location">Hobart, Tasmania, Australia</p>
      <ul class="contacts">
        <li>
          <svg viewBox="0 0 24 24" aria-hidden="true"><path d="M6.6 10.8a15.1 15.1 0 0 0 6.6 6.6l2.2-2.2c.3-.3.7-.4 1-.2 1.1.4 2.3.6 3.6.6.6 0 1 .4 1 1V20c0 .6-.4 1-1 1A17 17 0 0 1 3 4c0-.6.4-1 1-1h3.5c.6 0 1 .4 1 1 0 1.3.2 2.5.6 3.6.1.3 0 .7-.2 1z"/></svg>
          0400 123 456
        </li>
        <li>
          <svg viewBox="0 0 24 24" aria-hidden="true"><path d="M2 5h20v14H2z M3 6l9 7 9-7" fill="none" stroke="#1f9a48" stroke-width="2.4"/></svg>
          info@tmwhomecrafting.com.au
        </li>
        <li>
          <svg viewBox="0 0 24 24" aria-hidden="true"><circle cx="12" cy="12" r="10"/></svg>
          www.tmwhomecrafting.com.au
        </li>
      </ul>
    </div>
  </section>

  <section class="card card-back" aria-label="Business card back">
    <span class="back-mark"></span>
    <span class="back-name">TMW Home Crafting</span>
  </section>
</main>
</body>
</html>
```